Web landing page design

- Create a Web Design (Uncoded - PSD layout only)

We need a single web page design to promote our service. This page will
acts as a landing page for users and also be utilized in social media
advertising. Please provide us with a cutting edge design. I have attached
a link for what the company is about. In essence we are a photo checking
service which reviews photos for retailers, hotels abd car dealerships to
check everything is good after a service has been performed. Whether it be
a new promotion, cleaning or just checking prices. I am looking for a
design to say that we do many photos and at a very cost effective price
(team based in Mexico)

Link: https://slidevault.example/view/qTr8nWx2LpZk4mHcYdJs/
*Deadline*
5 days
*Updates*

- The Start Here box needs to look like this:

-Start Here (heading)
-A box for email addresses to be entered
-Then a check box with "Yes, I have read and agree to the Privacy Policy
and agree to receive email marketing from Plumora88'
-A submit button

All of this information needs to be in one box please. And please feel
free to contact me if you have any questions about this.

*Target Market(s)*
Retail business, Merchandising companies, Rental property owners, Car
dealers
Updates

Please can you submit entries. I am just looking for a tidy to a presentation already created. Just needs design touches.

Target Market(s)

Ability for audience to understand concept quickly
Benefits to why to use the product stand out
Technology driven approach

Industry/Entity Type

Retail

Number of Pages Required

1 page

Colors
0792cd

Requirements
Must have
• Clean and modern design

```html
<!DOCTYPE html>
<html lang="en">
<head>
<meta charset="utf-8">
<title>Clarivo – Transform retail execution with a simple photo</title>
<link rel="stylesheet" href="https://fonts.googleapis.com/css2?family=Montserrat:wght@400;500;600;700&display=swap">
<style>
:root{
  --brand:#0792cd;
  --brand-dark:#0677ad;
  --ink:#2b2b2b;
  --muted:#666;
  --card:#efefef;
  --footer:#3a3a3a;
  --white:#fff;
  --ring-fill:#e6f3fa;
}
*{box-sizing:border-box;margin:0;padding:0}
html,body{width:697px;height:1200px;overflow:hidden}
body{font-family:"Montserrat",sans-serif;color:var(--ink);background:var(--white);position:relative}
.abs{position:absolute}
.topline{left:0;top:0;width:697px;height:3px;background:var(--brand)}
.hero{left:0;top:3px;width:697px;height:402px;background:radial-gradient(ellipse at 62% 45%,#7b6a5c 0%,#3a3531 40%,#1c1c1e 80%),#1c1c1e}
.band{left:0;top:405px;width:697px;height:97px;background:linear-gradient(180deg,var(--brand),var(--brand-dark))}
.brand{left:57px;top:33px;display:flex;align-items:center;gap:7px;color:var(--white);font-weight:700;font-size:23px}
.brand-dot{width:20px;height:20px;border-radius:50%;background:var(--brand)}
.nav{top:38px;color:var(--white);font-size:12px;font-weight:500}
.start{left:57px;top:130px;width:188px;height:188px;border:2px solid #fff;background:rgba(240,240,240,.93);box-shadow:0 0 0 1px rgba(0,0,0,.15)}
.start h2{position:absolute;left:15px;top:27px;font-size:13px;font-weight:500;letter-spacing:.3px}
.start .email{position:absolute;left:15px;top:52px;width:156px;height:20px;background:#fff;border:1px solid #ddd;font-size:6px;color:#888;padding:6px 8px}
.start .consent{position:absolute;left:15px;top:82px;width:160px;font-size:6px;line-height:15px;color:#777}
.start .consent i{display:inline-block;width:6px;height:6px;background:var(--brand);margin-right:3px}
.start .submit{position:absolute;left:15px;top:133px;width:76px;height:21px;background:var(--brand);color:#fff;font-size:9px;font-weight:600;text-align:center;line-height:21px}
.headline{left:275px;top:190px;width:360px;text-align:center;color:#fff;font-size:24px;font-weight:700;line-height:32px;letter-spacing:.3px}
.stat{width:120px;text-align:center;color:#fff}
.stat .label{font-size:10px;line-height:13px;margin-top:6px}
.stat .num{position:absolute;left:0;top:0;width:84px;line-height:84px;text-align:center;color:var(--brand);font-size:17px;font-weight:700}
.ring{position:relative;width:84px;height:84px;margin:0 auto}
.card{top:525px;width:288px;height:210px;background:var(--card)}
.card h3{font-size:11px;font-weight:500;line-height:16px;letter-spacing:.2px}
.ticks{list-style:none;font-size:7px;color:var(--muted);line-height:16px}
.ticks li{position:relative;padding-left:11px;margin-bottom:3px}
.ticks li::before{content:"";position:absolute;left:0;top:4px;width:4px;height:2px;border-left:1.5px solid var(--brand);border-bottom:1.5px solid var(--brand);transform:rotate(-45deg)}
.blue-sm{color:var(--brand);font-size:8px;font-weight:500;line-height:15px}
.avatar{left:16px;top:67px;width:80px;height:80px;border-radius:50%;border:3px solid #fff;background:linear-gradient(#d9dde2,#9aa3ad)}
.phone{left:205px;top:57px;width:63px;height:127px;border-radius:9px;background:linear-gradient(#f3f3f3,#cfcfcf);border:1px solid #bbb}
.section-title{left:0;width:697px;text-align:center}
.photos{left:232px;top:848px;width:226px;height:124px;background:linear-gradient(90deg,#8c8c8c,#c9a48a 50%,#d7b6a8);border-radius:3px}
.tile{top:1004px;height:42px;border:1px solid #e5e5e5;background:#fff;display:flex;align-items:center;justify-content:center;font-size:11px;font-weight:700;color:var(--brand);white-space:nowrap}
.arrow{top:1016px;width:20px;height:20px;border-radius:50%;border:1px solid #e3e3e3}
.footer{left:0;top:1093px;width:697px;height:107px;background:var(--footer);color:#fff;text-align:center}
.social{position:absolute;top:16px;width:20px;height:20px;border-radius:50%;border:1px solid #fff}
.footer .links{position:absolute;top:50px;width:100%;font-size:8px}
.footer .copy{position:absolute;top:71px;width:100%;font-size:8px}
</style>
</head>
<body>
<div class="abs topline"></div>
<div class="abs hero" role="img" aria-label="Blurred photo of a hand holding a smartphone in a retail setting"></div>
<div class="abs band"></div>

<div class="abs brand"><span class="brand-dot"></span>Clarivo</div>
<div class="abs nav" style="left:315px">Home</div>
<div class="abs nav" style="left:385px">About</div>
<div class="abs nav" style="left:453px">Results</div>
<div class="abs nav" style="left:530px">How</div>
<div class="abs nav" style="left:589px">Free Trial</div>

<form class="abs start">
  <h2>START HERE</h2>
  <div class="email">Email Address</div>
  <p class="consent"><i></i>"Yes, I have read and agree to the Privacy Policy and agree to receive email marketing from Plumora88'</p>
  <div class="submit">SUBMIT</div>
</form>

<h1 class="abs headline">Transform Retail execution<br>with a simple photo</h1>

<div class="abs stat" style="left:57px;top:362px">
  <div class="ring"><svg width="84" height="84"><circle cx="42" cy="42" r="38" fill="var(--ring-fill)" stroke="#fff" stroke-width="4"/><path d="M42 4 A38 38 0 1 1 10 62" fill="none" stroke="var(--brand-dark)" stroke-width="4"/></svg><span class="num">2.2m</span></div>
  <div class="label">Photos Reviewed<br>Last year</div>
</div>
<div class="abs stat" style="left:203px;top:362px">
  <div class="ring"><svg width="84" height="84"><circle cx="42" cy="42" r="38" fill="var(--ring-fill)" stroke="#fff" stroke-width="4"/><path d="M42 4 A38 38 0 1 1 6 30" fill="none" stroke="#2b3d56" stroke-width="4"/></svg><span class="num">5p</span></div>
  <div class="label">From per Photo<br>Reviewd</div>
</div>
<div class="abs stat" style="left:355px;top:362px">
  <div class="ring"><svg width="84" height="84"><circle cx="42" cy="42" r="38" fill="var(--ring-fill)" stroke="#fff" stroke-width="4"/><path d="M42 4 A38 38 0 1 1 30 6" fill="none" stroke="#2b3d56" stroke-width="4"/></svg><span class="num">97.2%</span></div>
  <div class="label">Average Compliance</div>
</div>
<div class="abs stat" style="left:515px;top:362px">
  <div class="ring"><svg width="84" height="84"><circle cx="42" cy="42" r="38" fill="var(--ring-fill)" stroke="#fff" stroke-width="4"/><path d="M42 4 A38 38 0 1 1 8 58" fill="none" stroke="#2b3d56" stroke-width="4"/></svg><span class="num">3-8%</span></div>
  <div class="label">Sales Increase</div>
</div>

<section class="abs card" style="left:57px">
  <h3 class="abs" style="left:15px;top:30px">BORN OUT OF RETAIL EXECUTION</h3>
  <div class="abs avatar" role="img" aria-label="Portrait of the founder"></div>
  <div class="abs" style="left:112px;top:62px;width:170px">
    <p class="blue-sm">FOUNDER<br>MARCUS ELDWELL</p>
    <ul class="ticks" style="margin-top:6px">
      <li>18 yars of International retail experience</li>
      <li>Vice President Supply Chain Quillbrook Stores Canada</li>
      <li>Innovation Director - Brightline Merchandising UK</li>
    </ul>
  </div>
</section>

<section class="abs card" style="left:353px">
  <h3 class="abs" style="left:10px;top:20px">INCREASING SALES WITH A<br>SIMPLE PHOTO &amp; DIGITAL WORKFLOW</h3>
  <div class="abs" style="left:10px;top:60px;width:180px">
    <p class="blue-sm">3-8% sales with strong compliance</p>
    <ul class="ticks" style="margin-top:4px">
      <li>In minutes verify national promotions or range changes</li>
      <li>Real time insights why locations are not performing</li>
      <li>Elimintae field management audits.emails, calls with a digital workflow</li>
    </ul>
  </div>
  <div class="abs phone" role="img" aria-label="Smartphone showing a completed photo report"></div>
</section>

<h2 class="abs section-title" style="top:781px;font-size:12px;font-weight:500;letter-spacing:.3px">SERVING TOP RETAILERS AND BRANDS</h2>
<p class="abs section-title" style="top:810px;font-size:10px"><span style="color:var(--brand);font-size:15px;font-weight:700">2.2m</span> Photo's verified per year</p>
<div class="abs photos" role="img" aria-label="Stack of instant photos showing retail shelves and a hand using a tablet"></div>

<div class="abs arrow" style="left:51px"></div>
<div class="abs tile" style="left:86px;width:69px">Hammerly</div>
<div class="abs tile" style="left:170px;width:68px">Corvane</div>
<div class="abs tile" style="left:253px;width:94px">Greenfold</div>
<div class="abs tile" style="left:361px;width:68px">Pantrivo</div>
<div class="abs tile" style="left:443px;width:68px">Trolley&amp;Co</div>
<div class="abs tile" style="left:524px;width:87px">Maltory</div>
<div class="abs arrow" style="left:625px"></div>

<footer class="abs footer">
  <span class="social" style="left:301px"></span>
  <span class="social" style="left:326px"></span>
  <span class="social" style="left:351px"></span>
  <span class="social" style="left:376px"></span>
  <p class="links">Home &nbsp;| &nbsp;About &nbsp;| &nbsp;Results &nbsp;| &nbsp;How &nbsp;| &nbsp;Free trail</p>
  <p class="copy">Copyrights © 2018, Clarivo. All rights reserved. &nbsp;Sitemap | Terms | Privacy</p>
</footer>
</body>
</html>
```